Vision, Mission and Culture Posters

We have written text paragraphs for our company vision and mission and need them made into a2 or a3 sized posters using our logo for inspiration for colour. Our company culture has 10 paragraphs and we'd like this to be a single poster of a2 or a1. Each poster should have the logo on and share common design. It's not a complex job really.

Industry/Entity Type

It Company

Requirements
Nice to have
• These will be going up on our office wall so need to be clear to read from a distance and look professional but also not stodgy.

```html
<!DOCTYPE html>
<html lang="en">
<head>
<meta charset="utf-8">
<title>Bayline Parking Hire – Mission</title>
<link rel="stylesheet" href="https://fonts.googleapis.com/css2?family=Anton&family=Archivo+Black&family=Josefin+Sans:wght@400;700&family=Oswald:wght@700&family=Roboto+Condensed:wght@700&display=swap">
<style>
  :root {
    --brand-yellow: #fff200;
    --brand-red: #d2232a;
    --ink: #111111;
    --paper: #f6f6f4;
    --paper-edge: #efecc2;
    --white: #ffffff;
  }
  html, body {
    margin: 0;
    padding: 0;
    overflow: hidden;
    background: var(--paper);
  }
  h1, h2, p { margin: 0; }
  .poster {
    position: relative;
    width: 1200px;
    height: 849px;
    overflow: hidden;
    background: radial-gradient(ellipse 70% 65% at 50% 52%, var(--paper) 55%, var(--paper-edge) 100%);
    font-family: "Roboto Condensed", sans-serif;
    color: var(--ink);
  }
  .band {
    position: absolute;
    left: 0;
    width: 1200px;
  }
  .band--top { top: 0; height: 175px; }
  .band--bottom { bottom: 0; height: 45px; }

  .brand {
    position: absolute;
    left: 108px;
    top: 44px;
    display: flex;
    align-items: center;
    gap: 16px;
  }
  .brand__square {
    width: 64px;
    height: 64px;
    background: var(--brand-red);
  }
  .brand__name {
    font-family: "Roboto Condensed", sans-serif;
    font-weight: 700;
    font-size: 32px;
    line-height: 34px;
    color: var(--ink);
    letter-spacing: 1px;
  }

  .title-badge {
    position: absolute;
    left: 539px;
    top: 28px;
    width: 389px;
    height: 110px;
    background: var(--ink);
    border-radius: 12px;
    display: flex;
    align-items: center;
    justify-content: center;
    overflow: hidden;
  }
  .title-badge__text {
    margin: 0;
    font-family: "Anton", sans-serif;
    font-weight: 400;
    font-size: 100px;
    line-height: 110px;
    height: 110px;
    color: var(--brand-yellow);
    letter-spacing: 2px;
  }

  .mission-lead {
    position: absolute;
    left: 0;
    width: 1200px;
    top: 174px;
    text-align: center;
    font-family: "Archivo Black", sans-serif;
    font-size: 60px;
    line-height: 66px;
    letter-spacing: 1.5px;
  }
  .mission-goal {
    position: absolute;
    left: 0;
    width: 1200px;
    top: 244px;
    text-align: center;
    font-family: "Oswald", sans-serif;
    font-weight: 700;
    font-size: 58px;
    line-height: 66px;
    color: var(--brand-red);
    transform: scaleX(1.1);
    transform-origin: center;
  }
  .mission-scope {
    position: absolute;
    left: 0;
    width: 1200px;
    top: 311px;
    text-align: center;
    font-family: "Archivo Black", sans-serif;
    font-size: 28px;
    line-height: 34px;
    letter-spacing: -0.3px;
  }

  .belief-box {
    position: absolute;
    left: 35px;
    top: 368px;
    width: 1130px;
    height: 194px;
    box-sizing: border-box;
    background: var(--ink);
    border-radius: 14px;
    padding: 5px;
  }
  .belief-box__inner {
    height: 100%;
    box-sizing: border-box;
    background: var(--brand-red);
    border: 2px solid var(--white);
    border-radius: 10px;
    display: flex;
    align-items: center;
    justify-content: center;
  }
  .belief-box__text {
    text-align: center;
    font-family: "Josefin Sans", sans-serif;
    font-weight: 400;
    font-size: 41px;
    line-height: 46px;
    color: var(--white);
    padding-top: 6px;
  }
  .belief-box__text strong { font-weight: 700; }

  .method {
    position: absolute;
    left: 0;
    width: 1200px;
    top: 592px;
    text-align: center;
    font-family: "Roboto Condensed", sans-serif;
    font-weight: 700;
    font-size: 40px;
    line-height: 46px;
  }
</style>
</head>
<body>
<main class="poster">
  <svg class="band band--top" viewBox="0 0 1200 175" aria-hidden="true">
    <path d="M0 0 H1200 V64 C1130 120 1100 168 1045 168 C900 165 500 160 0 152 Z" fill="var(--brand-yellow)"/>
    <path d="M1200 64 C1130 120 1100 168 1045 168 C900 165 500 160 0 152" fill="none" stroke="var(--ink)" stroke-width="2"/>
  </svg>
  <svg class="band band--bottom" viewBox="0 0 1200 45" aria-hidden="true">
    <path d="M0 26 C500 20 900 10 1165 6 C1185 6 1195 12 1200 14 V45 H0 Z" fill="var(--brand-yellow)"/>
    <path d="M0 26 C500 20 900 10 1165 6 C1185 6 1195 12 1200 14" fill="none" stroke="var(--ink)" stroke-width="2"/>
  </svg>

  <div class="brand">
    <span class="brand__square" aria-hidden="true"></span>
    <span class="brand__name">Bayline Parking<br>Hire</span>
  </div>

  <div class="title-badge"><h1 class="title-badge__text">MISSION</h1></div>

  <p class="mission-lead">Our mission is to</p>
  <h2 class="mission-goal">ACHIEVE GREAT CUSTOMER SATISFACTION</h2>
  <p class="mission-scope">in everything we do and offer for meeting our customers parking needs.</p>

  <section class="belief-box">
    <div class="belief-box__inner">
      <p class="belief-box__text">We believe our path to achieving this comes through<br>giving a <strong>simple yet thorough and friendly service</strong> to<br>our customers without unnecessary complication.</p>
    </div>
  </section>

  <p class="method">We will achieve this through using the technology available to us,<br>continual staff training and development, regular refinement of our<br>practices and processes along with commitment to our roles and<br>the foundations for building our success.</p>
</main>
</body>
</html>
```